Brookvane Consulting Business Card Design

Business Card Design for Brookvane Consulting. Brookvane Consulting is a boutique consultancy based in Atlanta, GA., that specializes in marketing strategy, organization planning, and leadership development. We provide solutions for small businesses and startups as well as Vantage 300 companies.

http://brookvaneconsulting.com/

Target Market(s)

We provide solutions for small businesses and startups as well as Vantage 300 companies.

Industry/Entity Type

Consulting

Contact Information for Business Card

Two sided business card with priority on contact information, logo, tag line (Inspiration to Dream More, Do More, Become More)

Colors

Designer to choose colors to be used in the design.

Requirements
Must have
• contact information, logo, tag line (Inspiration to Dream More, Do More, Become More)
• Simple no over communication.
Nice to have
• I would like to see different placements of logo and creative use of both sides of the card
Should not have
• Do not put too much information on the card.

```html
<!DOCTYPE html>
<html lang="en">
<head>
<meta charset="utf-8">
<title>Brookvane Consulting Business Card</title>
<link href="https://fonts.googleapis.com/css2?family=Roboto:wght@400;500;700&family=Roboto+Condensed:wght@700&display=swap" rel="stylesheet">
<style>
  :root {
    --backdrop: #2a2a2b;
    --card: #1c1c1d;
    --ink: #f2f2f2;
    --ink-muted: #b9b9b9;
    --divider: #7a7a7a;
  }
  * { box-sizing: border-box; margin: 0; padding: 0; }
  html, body {
    width: 1200px;
    height: 900px;
    overflow: hidden;
    background: var(--backdrop);
  }
  .canvas {
    position: relative;
    width: 1200px;
    height: 900px;
  }
  .card {
    position: absolute;
    left: 260px;
    width: 680px;
    height: 388px;
    background: var(--card);
    box-shadow: 0 14px 30px rgba(0,0,0,0.45);
    color: var(--ink);
  }
  .card--front { top: 50px; }
  .card--back { top: 474px; }

  /* Front */
  .brand {
    position: absolute;
    top: 112px;
    left: 0;
    right: 0;
    text-align: center;
    font-family: "Roboto", sans-serif;
    font-weight: 500;
    font-size: 50px;
    letter-spacing: 1px;
    color: var(--ink);
  }
  .brand__mark {
    display: inline-block;
    width: 14px;
    height: 14px;
    margin-left: 10px;
    background: var(--ink);
    vertical-align: middle;
  }
  .brand__sub {
    display: block;
    margin-top: 6px;
    font-size: 26px;
    letter-spacing: 6px;
    text-transform: uppercase;
  }
  .tagline {
    position: absolute;
    top: 268px;
    left: 0;
    right: 0;
    text-align: center;
    font-family: "Roboto", sans-serif;
    font-weight: 500;
    font-size: 17px;
    color: var(--ink);
  }

  /* Back */
  .identity {
    position: absolute;
    top: 150px;
    right: 390px;
    text-align: right;
  }
  .identity__name {
    font-family: "Roboto Condensed", sans-serif;
    font-weight: 700;
    font-size: 30px;
    color: var(--ink-muted);
    text-transform: uppercase;
    line-height: 1;
  }
  .identity__role {
    margin-top: 6px;
    font-family: "Roboto", sans-serif;
    font-weight: 500;
    font-size: 17px;
    color: var(--ink);
  }
  .divider {
    position: absolute;
    left: 306px;
    top: 140px;
    width: 1px;
    height: 98px;
    background: var(--divider);
  }
  .contacts {
    position: absolute;
    left: 330px;
    top: 150px;
    list-style: none;
    font-family: "Roboto", sans-serif;
    font-weight: 500;
    font-size: 18px;
    color: var(--ink);
  }
  .contacts__item {
    display: flex;
    align-items: center;
    gap: 10px;
    height: 26px;
  }
  .contacts__icon {
    width: 15px;
    height: 15px;
    fill: var(--ink-muted);
    flex: none;
  }
</style>
</head>
<body>
<main class="canvas">
  <section class="card card--front" aria-label="Card front">
    <h1 class="brand">Brookvane<span class="brand__mark" aria-hidden="true"></span><span class="brand__sub">Consulting</span></h1>
    <p class="tagline">Inspiration to Dream More, Do More, Become More</p>
  </section>

  <section class="card card--back" aria-label="Card back">
    <div class="identity">
      <p class="identity__name">Marcus Hale</p>
      <p class="identity__role">Founder/Managing Director</p>
    </div>
    <div class="divider" aria-hidden="true"></div>
    <ul class="contacts">
      <li class="contacts__item">
        <svg class="contacts__icon" viewBox="0 0 24 24" aria-hidden="true"><path d="M6.6 10.8a15.1 15.1 0 0 0 6.6 6.6l2.2-2.2a1 1 0 0 1 1-.25 11.4 11.4 0 0 0 3.6.57 1 1 0 0 1 1 1V20a1 1 0 0 1-1 1A17 17 0 0 1 3 4a1 1 0 0 1 1-1h3.5a1 1 0 0 1 1 1c0 1.25.2 2.45.57 3.6a1 1 0 0 1-.25 1z"/></svg>
        <span>424-555-0142</span>
      </li>
      <li class="contacts__item">
        <svg class="contacts__icon" viewBox="0 0 24 24" aria-hidden="true"><path d="M2 5h20v14H2z M3.5 6.5 12 12.5l8.5-6v-.01H3.5z" fill-rule="evenodd"/></svg>
        <span>marcus@brookvaneconsulting.com</span>
      </li>
      <li class="contacts__item">
        <svg class="contacts__icon" viewBox="0 0 24 24" aria-hidden="true"><circle cx="12" cy="12" r="10"/><path d="M2 12h20M12 2c3 3 3 17 0 20M12 2c-3 3-3 17 0 20" stroke="#1c1c1d" stroke-width="1.6" fill="none"/></svg>
        <span>brookvaneconsulting.com</span>
      </li>
    </ul>
  </section>
</main>
</body>
</html>
```